Varnel Corporate Website for technological company

We need a modern website to promote our product and services.
You can found the actually website at the address: www.varnel-example.ch

We are a new company for B2B market. We would like do show our high precision and innovation capability.

we need a section were is possible to easily upload "news" and documents for our customers.

Target Market(s)

B2B services in the industry market

Industry/Entity Type

It Company

Coding

Coded - Design and coding required

Number of Pages Required

5+ page

Font styles to use
Other font styles liked:
• We accept propositions

Requirements
Must have
• Easy to maintain
• Presentation of the Varnel company
• Presentation of Varnel services and products
• The customer can download our ducumentation
Nice to have
• Sexy and modern

```html
<!DOCTYPE html>
<html lang="en">
<head>
<meta charset="utf-8">
<title>Varnel Sàrl</title>
<link href="https://fonts.googleapis.com/css2?family=Exo+2:wght@600;700&family=Arimo:wght@400;700&display=swap" rel="stylesheet">
<style>
:root{
  --olive:#a39a45;
  --olive-dark:#8e8638;
  --ink:#2b2b2b;
  --text:#6d6d6d;
  --muted:#8a8a8a;
  --light:#f4f5f6;
  --line:#e6e6e6;
  --footer:#2f2f2f;
  --white:#ffffff;
}
*{box-sizing:border-box;margin:0;padding:0}
html,body{width:1200px;height:2786px;overflow:hidden;background:var(--white)}
body{font-family:"Arimo",Arial,sans-serif;color:var(--text);position:relative}
.abs{position:absolute}
.heading{font-family:"Exo 2",sans-serif;font-weight:700;font-size:21px;color:#3a3a3a;text-align:center;letter-spacing:.5px;width:1200px;left:0}
.heading span{color:var(--olive)}
.lead{font-size:12px;line-height:23px;text-align:center;color:#777;width:660px;left:270px}
.brand{font-family:"Exo 2",sans-serif;font-weight:700;color:var(--ink);display:flex;align-items:center;gap:8px}
.brand-mark{background:var(--olive);display:inline-block}

/* header */
.topline{top:0;left:0;width:1200px;height:4px;background:var(--olive)}
.site-header{top:4px;left:0;width:1200px;height:81px;background:var(--white);box-shadow:0 1px 3px rgba(0,0,0,.08);z-index:2}
.site-header .brand{position:absolute;left:85px;top:24px;font-size:28px}
.site-header .brand-mark{width:26px;height:26px}
.site-header .brand small{font-size:12px;margin-left:2px}
.nav{position:absolute;left:0;top:34px;width:1060px;height:16px;font-size:11.5px;text-transform:uppercase}
.nav a{position:absolute;top:0;color:#333;text-decoration:none;white-space:nowrap}
.nav a.active{color:var(--olive)}
.search{position:absolute;left:1073px;top:22px;width:40px;height:40px;border-radius:50%;background:var(--olive)}

/* hero */
.hero{top:85px;left:0;width:1200px;height:476px;background:linear-gradient(90deg,#f2f2f2,#fafafa 40%,#e9e9e9)}
.hero-photo{position:absolute;left:436px;top:0;width:764px;height:476px;background:linear-gradient(90deg,rgba(240,240,240,0),#9a9ea3 35%,#3c3f44 70%,#23262a)}
.hero .brand{position:absolute;left:85px;top:150px;font-size:60px}
.hero .brand-mark{width:56px;height:56px}
.hero .brand small{font-size:20px;align-self:flex-end;margin-bottom:10px}
.hero-text{position:absolute;left:85px;top:230px;width:315px;font-size:11.5px;line-height:22px;color:#555}
.btn{position:absolute;background:var(--olive);color:#fff;font-family:"Exo 2",sans-serif;font-weight:700;font-size:13px;display:flex;align-items:center;justify-content:center;border-radius:3px}
.hero .btn{left:85px;top:338px;width:115px;height:36px;box-shadow:0 2px 3px rgba(0,0,0,.25)}

/* services */
.service{position:absolute;top:711px;width:242px;height:307px;border:1px solid var(--line);background:#fff;text-align:center;box-shadow:0 8px 6px -6px rgba(0,0,0,.25)}
.service .icon{width:108px;height:108px;border-radius:50%;background:var(--olive);margin:22px auto 0;display:flex;align-items:center;justify-content:center}
.service h3{font-family:"Exo 2",sans-serif;font-weight:600;font-size:13px;color:var(--olive);margin-top:26px;text-transform:uppercase;letter-spacing:.3px}
.service p{font-size:11.5px;line-height:23px;color:#777;margin:12px 22px 0}
.more{font-family:"Exo 2",sans-serif;font-weight:700;font-size:12px;color:var(--olive);text-decoration:underline}
.service .more{display:block;margin-top:14px}

/* products */
.products-band{top:1053px;left:0;width:1200px;height:457px;background:var(--light)}
.product{position:absolute;top:1198px;width:245px;height:277px;background:#fff;overflow:hidden;text-align:center;color:#fff}
.product .photo{position:absolute;left:40px;top:22px;width:165px;height:130px;border-radius:8px;background:radial-gradient(circle,#8d8d86,#d9d9d3 70%,#fff)}
.product svg{position:absolute;left:0;top:152px}
.product h3{position:absolute;top:192px;width:100%;font-family:"Exo 2",sans-serif;font-weight:700;font-size:15px;text-transform:uppercase}
.product p{position:absolute;top:218px;width:100%;font-size:11.5px}
.product .stars{position:absolute;top:236px;width:100%;font-size:13px;letter-spacing:1px}

/* blog */
.post{position:absolute;top:1649px;width:325px}
.post .photo{height:202px;background:linear-gradient(135deg,#d8d8d8,#4b4b4b 60%,#1b1b1b)}
.post h3{font-family:"Exo 2",sans-serif;font-weight:700;font-size:14.5px;color:#333;margin-top:29px;text-transform:uppercase}
.post .meta{font-size:12px;color:#888;margin-top:14px;display:flex;gap:18px;align-items:center}
.post .excerpt{font-size:11.5px;line-height:23px;color:#777;margin-top:10px}
.post .more{display:block;margin-top:23px}

/* testimonials */
.testimonials{top:2098px;left:0;width:1200px;height:379px;background:var(--olive)}
.testimonials .heading,.testimonials .lead{color:#fff}
.testi{position:absolute;top:2264px;width:330px;color:#fff}
.avatar{position:absolute;left:0;top:0;width:86px;height:86px;border-radius:50%;border:3px solid #fff;background:linear-gradient(#d9c9a8,#b59d74)}
.testi .quote{position:absolute;left:110px;top:0;width:220px;font-size:11.5px;line-height:23px}
.testi .quote b{font-family:Georgia,serif;font-size:20px;margin-right:6px}
.testi .author{position:absolute;left:110px;top:116px;font-family:"Exo 2",sans-serif;font-weight:700;font-size:12px}
.testi .date{position:absolute;left:110px;top:138px;font-size:11px}
.testi .stars{position:absolute;left:110px;top:156px;font-size:12px}

/* footer */
.site-footer{top:2477px;left:0;width:1200px;height:309px;background:var(--footer);color:#fff}
.site-footer .brand{position:absolute;left:85px;top:120px;font-size:40px;color:#fff}
.site-footer .brand-mark{width:36px;height:36px}
.site-footer .brand small{font-size:15px;align-self:flex-end;margin-bottom:6px}
.fcol h4{font-family:"Exo 2",sans-serif;font-weight:700;font-size:16px;letter-spacing:.3px}
.contact-list{list-style:none;margin-top:22px;font-size:11.5px}
.contact-list li{display:flex;gap:12px;align-items:flex-start;height:30px}
.contact-list svg{flex:none;margin-top:1px}
.fcol p{font-size:11.5px;line-height:21px;margin-top:20px}
.field{margin-top:14px;width:208px;height:32px;background:#fff;color:#888;font-size:12px;padding:9px 12px}
.site-footer .btn{position:relative;width:80px;height:24px;font-size:10px;margin-top:10px;border-radius:2px}
.socials{display:flex;gap:8px;margin-top:14px}
.socials span{width:37px;height:37px;border-radius:50%;border:2px solid #fff}
.copyright{position:absolute;top:272px;width:1200px;text-align:center;font-size:12px}
</style>
</head>
<body>

<div class="abs topline"></div>
<header class="abs site-header">
  <div class="brand"><span class="brand-mark"></span>Varnel <small>Sàrl</small></div>
  <nav class="nav">
    <a class="active" style="left:496px">Home</a>
    <a style="left:572px">Services</a>
    <a style="left:671px">Products</a>
    <a style="left:777px">Examples</a>
    <a style="left:883px">Download</a>
    <a style="left:995px">Contacts</a>
  </nav>
  <div class="search">
    <svg width="40" height="40" viewBox="0 0 40 40"><circle cx="18.5" cy="18.5" r="5" fill="none" stroke="#fff" stroke-width="2"/><line x1="22" y1="22" x2="26" y2="26" stroke="#fff" stroke-width="2.5" stroke-linecap="round"/></svg>
  </div>
</header>

<section class="abs hero">
  <div class="hero-photo" role="img" aria-label="Two businessmen in suits reviewing a tablet"></div>
  <div class="brand"><span class="brand-mark"></span>Varnel <small>Sàrl</small></div>
  <p class="hero-text">The ever-increasing complexity in modern systems, the search for reliability and performance and the continuous desire to reduce production costs &amp; intesoftware and me systems in which electronics chanical systems.</p>
  <div class="btn">READ MORE</div>
</section>

<section>
  <h2 class="abs heading" style="top:592px">OUR <span>SERVICES</span></h2>
  <p class="abs lead" style="top:631px">The ever-increasing complexity in modern systems, the search for reliability and performance and the continuous integra-tion between the electronic units, software and mechanical systems.</p>

  <article class="service" style="left:85px">
    <div class="icon"><svg width="56" height="44" viewBox="0 0 56 44" fill="none" stroke="#fff" stroke-width="2.5"><rect x="8" y="3" width="40" height="28" rx="2"/><path d="M2 36h52l-4 5H6z"/><path d="M28 10l8 4v8l-8 4-8-4v-8z"/></svg></div>
    <h3>Simulation &amp; Modeling</h3>
    <p>The ever-increasing complexity in modern systems, the search for reliability software and mechanical systems.</p>
    <span class="more">READ MORE</span>
  </article>
  <article class="service" style="left:347px">
    <div class="icon"><svg width="50" height="50" viewBox="0 0 50 50" fill="#fff"><path d="M30 6l14 14-10 10-14-14z"/><rect x="34" y="2" width="4" height="12" transform="rotate(45 36 8)"/><rect x="42" y="10" width="4" height="12" transform="rotate(45 44 16)"/><path d="M22 22l6 6-16 16-6-6z"/></svg></div>
    <h3>Electronics</h3>
    <p>The ever-increasing complexity in modern systems, the search for reliability software and mechanical systems.</p>
    <span class="more">READ MORE</span>
  </article>
  <article class="service" style="left:609px">
    <div class="icon"><svg width="60" height="60" viewBox="0 0 60 60" fill="none" stroke="#fff" stroke-width="3"><circle cx="30" cy="30" r="18" stroke-dasharray="6 4" stroke-width="7"/><circle cx="30" cy="30" r="9"/></svg></div>
    <h3>Mechanics</h3>
    <p>The ever-increasing complexity in modern systems, the search for reliability software and mechanical systems.</p>
    <span class="more">READ MORE</span>
  </article>
  <article class="service" style="left:871px">
    <div class="icon"><svg width="54" height="54" viewBox="0 0 54 54" fill="none" stroke="#fff" stroke-width="2.5"><path d="M6 16l20-10 20 10v22l-20 10-20-10z"/><path d="M6 16l20 10 20-10M26 26v22"/><circle cx="38" cy="38" r="9" fill="var(--olive)"/><path d="M38 33v7m0 0l-3-3m3 3l3-3"/></svg></div>
    <h3>Software</h3>
    <p>The ever-increasing complexity in modern systems, the search for reliability software and mechanical systems.</p>
    <span class="more">READ MORE</span>
  </article>
</section>

<section>
  <div class="abs products-band"></div>
  <h2 class="abs heading" style="top:1081px">OUR <span>PRODUCTS</span></h2>
  <p class="abs lead" style="top:1120px">The ever-increasing complexity in modern systems, the search for reliability and performance and the continuous integra-tion between the electronic units, software and mechanical systems.</p>

  <article class="product" style="left:85px">
    <div class="photo" role="img" aria-label="Electric starter motor"></div>
    <svg width="245" height="125" viewBox="0 0 245 125"><path d="M0 30 Q122 0 245 30 V125 H0z" fill="var(--olive)"/></svg>
    <h3>Kestrel</h3><p>Increasing complexity in modern systems</p><div class="stars">☆☆☆☆☆</div>
  </article>
  <article class="product" style="left:347px">
    <div class="photo" role="img" aria-label="Green circuit board with display" style="background:radial-gradient(circle,#3f7a4a,#b9cdb9 70%,#fff)"></div>
    <svg width="245" height="125" viewBox="0 0 245 125"><path d="M0 30 Q122 0 245 30 V125 H0z" fill="var(--olive)"/></svg>
    <h3>Tessa</h3><p>Increasing complexity in modern systems</p><div class="stars">☆☆☆☆☆</div>
  </article>
  <article class="product" style="left:609px">
    <div class="photo" role="img" aria-label="Cylindrical fuel pump"></div>
    <svg width="245" height="125" viewBox="0 0 245 125"><path d="M0 30 Q122 0 245 30 V125 H0z" fill="var(--olive)"/></svg>
    <h3>Kestrel</h3><p>Increasing complexity in modern systems</p><div class="stars">☆☆☆☆☆</div>
  </article>
  <article class="product" style="left:868px">
    <div class="photo" role="img" aria-label="Servo motor with connectors" style="background:radial-gradient(circle,#3a3a3a,#c9c9c9 70%,#fff)"></div>
    <svg width="245" height="125" viewBox="0 0 245 125"><path d="M0 30 Q122 0 245 30 V125 H0z" fill="var(--olive)"/></svg>
    <h3>Kestrel</h3><p>Increasing complexity in modern systems</p><div class="stars">☆☆☆☆☆</div>
  </article>
</section>

<section>
  <h2 class="abs heading" style="top:1539px">LATEST <span>BLOG</span></h2>
  <p class="abs lead" style="top:1578px">The ever-increasing complexity in modern systems, the search for reliability and performance and the continuous integra-tion between the electronic units, software and mechanical systems.</p>

  <article class="post" style="left:85px">
    <div class="photo" role="img" aria-label="Precision optical inspection equipment"></div>
    <h3>Intelligent Controller Multi</h3>
    <div class="meta"><span>▦ 20 Sep 2016</span><span>|</span><span>◌ Comments (05)</span></div>
    <p class="excerpt">The ever-increasing complexity in modern systems, the search for reliability and performance and the continuous integration software and mechanical systems.</p>
    <span class="more">READ MORE »</span>
  </article>
  <article class="post" style="left:438px">
    <div class="photo" role="img" aria-label="Open hard disk drive mechanism" style="background:linear-gradient(135deg,#e2e2e2,#9a9a9a 50%,#6a4a2a)"></div>
    <h3>Intelligent Controller Multi</h3>
    <div class="meta"><span>▦ 20 Sep 2016</span><span>|</span><span>◌ Comments (05)</span></div>
    <p class="excerpt">The ever-increasing complexity in modern systems, the search for reliability and performance and the continuous integration software and mechanical systems.</p>
    <span class="more">READ MORE »</span>
  </article>
  <article class="post" style="left:789px">
    <div class="photo" role="img" aria-label="Close-up of mechanical gears" style="background:linear-gradient(135deg,#1d1d1d,#4a4a4a 45%,#c9a21c 60%,#222)"></div>
    <h3>Intelligent Controller Multi</h3>
    <div class="meta"><span>▦ 20 Sep 2016</span><span>|</span><span>◌ Comments (05)</span></div>
    <p class="excerpt">The ever-increasing complexity in modern systems, the search for reliability and performance and the continuous integration software and mechanical systems.</p>
    <span class="more">READ MORE »</span>
  </article>
</section>

<section class="abs testimonials">
  <h2 class="abs heading" style="top:58px">OUR TESTIMONIALS</h2>
  <p class="abs lead" style="top:96px">The ever-increasing complexity in modern systems, the search for reliability and performance and the continuous integra-tion between the electronic units, software and mechanical systems.</p>
  <svg class="abs" style="left:40px;top:184px" width="20" height="110" viewBox="0 0 20 110"><path d="M18 2L2 55l16 53" fill="none" stroke="#fff" stroke-opacity=".6" stroke-width="1.5"/></svg>
  <svg class="abs" style="left:1140px;top:184px" width="20" height="110" viewBox="0 0 20 110"><path d="M2 2l16 53L2 108" fill="none" stroke="#fff" stroke-opacity=".6" stroke-width="1.5"/></svg>
</section>
<div class="testi" style="left:85px">
  <div class="avatar" role="img" aria-label="Customer portrait"></div>
  <p class="quote"><b>“</b>The ever-increasing complexity in modern systems, the search for reliabil-ity and performance and the continuous software and mechanical systems.</p>
  <div class="author">JON CARTER</div><div class="date">POSTED ON 25 AUG 2016</div><div class="stars">☆☆☆☆☆</div>
</div>
<div class="testi" style="left:436px">
  <div class="avatar" role="img" aria-label="Customer portrait"></div>
  <p class="quote"><b>“</b>The ever-increasing complexity in modern systems, the search for reliabil-ity and performance and the continuous software and mechanical systems.</p>
  <div class="author">JON CARTER</div><div class="date">POSTED ON 25 AUG 2016</div><div class="stars">☆☆☆☆☆</div>
</div>
<div class="testi" style="left:787px">
  <div class="avatar" role="img" aria-label="Customer portrait"></div>
  <p class="quote"><b>“</b>The ever-increasing complexity in modern systems, the search for reliabil-ity and performance and the continuous software and mechanical systems.</p>
  <div class="author">JON CARTER</div><div class="date">POSTED ON 25 AUG 2016</div><div class="stars">☆☆☆☆☆</div>
</div>

<footer class="abs site-footer">
  <div class="brand"><span class="brand-mark"></span>Varnel <small>Sàrl</small></div>

  <div class="abs fcol" style="left:414px;top:40px">
    <h4>CONTACT US</h4>
    <ul class="contact-list">
      <li><svg width="14" height="12" viewBox="0 0 14 12" fill="#fff"><path d="M1 3c0-2 12-2 12 0v2h-3V3H4v2H1z"/><rect x="2" y="6" width="10" height="6" rx="1"/></svg>+41 (0)00 555 01 23 (Phone)</li>
      <li><svg width="14" height="12" viewBox="0 0 14 12" fill="#fff"><rect x="3" y="0" width="8" height="4"/><rect x="0" y="4" width="14" height="6" rx="1"/><rect x="3" y="8" width="8" height="4" fill="#2f2f2f" stroke="#fff"/></svg>+41 (0)00 555 01 23 (Fax)</li>
      <li><svg width="14" height="10" viewBox="0 0 14 10"><rect x=".5" y=".5" width="13" height="9" fill="none" stroke="#fff"/><path d="M1 1l6 5 6-5" fill="none" stroke="#fff"/></svg><u>info@varnel.ch (Email)</u></li>
      <li><svg width="14" height="14" viewBox="0 0 14 14" fill="#fff"><path d="M7 0a5 5 0 0 1 5 5c0 4-5 9-5 9S2 9 2 5a5 5 0 0 1 5-5z"/><circle cx="7" cy="5" r="2" fill="#2f2f2f"/></svg><span>Chemin des Vergers 4<br>CH - 1000 Valmont</span></li>
    </ul>
  </div>

  <div class="abs fcol" style="left:650px;top:40px">
    <h4>NEWSLETTER</h4>
    <p style="width:215px">Register Your email address to get information ablout us</p>
    <div class="field">Email Address</div>
    <div class="btn">SUBSCRIBE</div>
  </div>

  <div class="abs fcol" style="left:906px;top:40px">
    <h4>FOLLOW US</h4>
    <p style="width:215px">Lorem ipsum dolor sit amet, conse ctetur adipiscing elit. Nulla in purus nibh. Donec ornare</p>
    <div class="socials" aria-label="Social media links">
      <span></span><span></span><span></span><span></span><span></span>
    </div>
  </div>

  <div class="copyright">Copyright © varnel. All rights reserved</div>
</footer>

</body>
</html>
```